Realty Group Needs Classy, Contemporary Letterhead Design

We need a letterhead design for a new realty company located in NY, USA. We buy investment properties to rehabilitate and or keep in our rental portfolio.

```html
<!DOCTYPE html>
<html lang="en">
<head>
<meta charset="utf-8">
<title>Halvorsen Realty Group — Letterhead</title>
<link href="https://fonts.googleapis.com/css2?family=Poppins:wght@400;600;700&family=Didact+Gothic&display=swap" rel="stylesheet">
<style>
  :root {
    --purple: #4b2a85;
    --header-grey: #7b7a79;
    --paper-light: #f1f1f1;
    --paper-dark: #e0e0e0;
    --ink: #2a2a2a;
    --body-ink: #3a3a3a;
    --lavender: #c9bfdb;
    --white: #ffffff;
  }
  * { margin: 0; padding: 0; box-sizing: border-box; }
  html, body { width: 960px; height: 1200px; overflow: hidden; }
  body {
    position: relative;
    background: linear-gradient(100deg, var(--paper-light) 0%, var(--paper-dark) 100%);
    font-family: "Didact Gothic", sans-serif;
    color: var(--ink);
  }
  .header-band { position: absolute; top: 0; left: 0; width: 520px; height: 148px; }
  .brand {
    position: absolute; top: 52px; left: 60px; width: 300px; text-align: center;
  }
  .brand-name {
    font-family: "Poppins", sans-serif; font-weight: 700; font-size: 40px;
    line-height: 1; color: var(--purple); letter-spacing: -0.5px;
  }
  .brand-sub {
    display: flex; align-items: center; gap: 8px; margin-top: 6px;
    font-family: "Poppins", sans-serif; font-weight: 600; font-size: 14px;
    color: var(--white); letter-spacing: 0.8px; white-space: nowrap;
  }
  .brand-sub::before, .brand-sub::after {
    content: ""; flex: 1; height: 2px; background: var(--white);
  }
  .contact {
    position: absolute; top: 70px; right: 86px; text-align: right;
    font-family: "Poppins", sans-serif; font-size: 14px; line-height: 18px; color: var(--ink);
  }
  .contact .company { color: var(--purple); font-weight: 600; }
  .contact .address { margin-bottom: 22px; }
  .contact .label { color: var(--purple); font-weight: 600; margin-right: 4px; }
  .watermark { position: absolute; left: 40px; top: 640px; width: 900px; height: 560px; }
  .letter { position: absolute; top: 352px; left: 88px; width: 792px; }
  .greeting { font-size: 22px; margin-bottom: 34px; color: var(--ink); }
  .letter p.body {
    font-size: 13.4px; line-height: 20.5px; color: var(--body-ink);
    text-align: justify; margin-bottom: 20px;
  }
  .closing { font-size: 13.4px; margin-top: 34px; color: var(--body-ink); }
  .signature { display: block; margin-top: 18px; }
  .footer-band { position: absolute; right: 0; bottom: 0; width: 360px; height: 48px; }
  .footer-url {
    position: absolute; right: 36px; bottom: 14px;
    font-family: "Poppins", sans-serif; font-weight: 600; font-size: 15px;
    letter-spacing: 3.5px; color: var(--white);
  }
</style>
</head>
<body>
  <svg class="header-band" viewBox="0 0 520 148" aria-hidden="true">
    <path d="M0 0 H520 C470 0 455 50 438 90 C418 135 385 148 340 148 H0 Z" fill="var(--header-grey)"/>
  </svg>

  <div class="brand">
    <div class="brand-name">HALVORSEN</div>
    <div class="brand-sub">Realty Group, LLC</div>
  </div>

  <address class="contact" style="font-style:normal">
    <div class="company">Halvorsen LLC</div>
    <div class="address">1420 Linden<br>Lane Albany<br>New York 12205</div>
    <div><span class="label">T</span>: 555-214-7730</div>
    <div><span class="label">C</span>: 555-318-4092</div>
    <div><span class="label">F</span>: 555-627-1845</div>
    <div><span class="label">E</span>: info@halvorsenrealty.com</div>
  </address>

  <svg class="watermark" viewBox="0 0 900 560" role="img" aria-label="Faint large brand decoration area">
    <defs>
      <radialGradient id="wm-fade" cx="0.6" cy="0.7" r="0.6">
        <stop offset="0" stop-color="var(--lavender)" stop-opacity="0.55"/>
        <stop offset="1" stop-color="var(--lavender)" stop-opacity="0"/>
      </radialGradient>
    </defs>
    <rect width="900" height="560" fill="url(#wm-fade)"/>
  </svg>

  <main class="letter">
    <p class="greeting">Dear Mr. Carter,</p>
    <p class="body">Lorem ipsum dolor sit amet, consectetur adipiscing elit. Donec orci purus, luctus vitae dignissim eu, iaculis sed purus. Vivamus faucibus, ipsum nec aliquet viverra, leo mauris condimentum ligula, sit amet sagittis enim ligula quis arcu. Nam egestas tortor id nisi porttitor mattis. In tortor ante, ultricies in suscipit a, tempus non massa. Vivamus et auctor mi. Fusce vel massa nulla. Phasellus nec eros mauris, et scelerisque orci.</p>
    <p class="body">Donec malesuada orci vitae nulla accumsan porta a id massa. Quisque accumsan iaculis magna sit amet fringilla. Maecenas consequat, magna eget tincidunt semper, odio nibh rutrum mi, id feugiat ante nisi eu risus. Vestibulum nunc orci, rhoncus a placerat in, ultricies in mi. Cras mattis varius eros, vel fringilla nisi suscipit eget. Quisque scelerisque sagittis nulla at porttitor.</p>
    <p class="body">Sed id augue vitae urna euismod commodo aliquet a quam. Pellentesque arcu velit, cursus et malesuada ut, consequat et diam. Nullam erat sem, rhoncus id ullamcorper vitae, rhoncus et arcu. In ultricies ultricies nulla, ut rutrum nisi iaculis at. Donec eu magna a metus ornare faucibus. Fusce aliquet faucibus ultricies. Morbi semper, est id tincidunt gravida, sem arcu adipiscing lacus, ac bibendum nulla leo eu purus. Quisque nec diam sed risus consectetur a ccumsan quis quis nibh. Vestibulum id purus lorem.</p>
    <p class="body">It is a long established fact that a reader will be distracted by the readable content of a page when looking at its layout. The point of using Lorem Ipsum is that it has a more-or-less normal distribution of letters, as opposed to using 'Content here, content here', making it look like readable English. Many desktop publishing packages</p>
    <p class="closing">Sincerely,</p>
    <svg class="signature" width="130" height="72" viewBox="0 0 130 72" role="img" aria-label="Handwritten signature">
      <rect width="130" height="72" rx="4" fill="#d6d6d6" fill-opacity="0.5"/>
    </svg>
  </main>

  <svg class="footer-band" viewBox="0 0 360 48" aria-hidden="true">
    <path d="M0 48 C14 48 18 40 24 26 C30 10 36 0 52 0 H360 V48 Z" fill="var(--purple)"/>
  </svg>
  <div class="footer-url">WWW.HALVORSENREALTY.COM</div>
</body>
</html>
```